Letterhead and matching envelope design for a dental office

We need a new stationary design, letterhead and envelope #10, for a dental office in Denver area. We are called Bright Harbor Dental. We want a simple and minimalistic design but not a boring design. I wish to have one good point that makes it look professional. I have attached our logo. Feel free to use either one. I want the design for letterhead and envelope look like a "matching pair" but not look the same. The envelope doesn't have to be white and it will have an address window on bottom left.

Target Market(s)

everyone who visits dentist (adults)

Industry/Entity Type

Dental

Font styles to use
Other font styles liked:
• close to font on logo or something that matches well

Requirements
Must have
• professional
• simple, minimalistic
• unique point that stands out
Nice to have
• matching but not same design for letterhead and envelope
Should not have
• not look like all the other boring designs
• no flowery, distracting feats

```html
<!DOCTYPE html>
<html lang="en">
<head>
<meta charset="utf-8">
<title>Bright Harbor Dental — Letterhead</title>
<link rel="stylesheet" href="https://fonts.googleapis.com/css2?family=Open+Sans:wght@400;600&family=Arimo:wght@400;700&display=swap">
<style>
  :root {
    --bg: #e6e6e8;
    --paper: #ffffff;
    --green: #3ab54a;
    --green-light: #a9d9a8;
    --green-pale: #eef6ec;
    --text: #555a5e;
    --heading: #4a4f53;
  }
  * { margin: 0; padding: 0; box-sizing: border-box; }
  html, body { width: 1200px; height: 1066px; overflow: hidden; background: var(--bg); }
  .letterhead {
    position: absolute; left: 246px; top: 33px;
    width: 707px; height: 1000px;
    background: var(--paper);
    box-shadow: 0 4px 18px rgba(0,0,0,.12);
    overflow: hidden;
    font-family: "Arimo", Arial, sans-serif;
    color: var(--text);
  }
  .brand {
    position: absolute; left: 52px; top: 52px;
    display: flex; align-items: center; gap: 10px;
  }
  .brand-dot { width: 14px; height: 14px; border-radius: 50%; background: var(--green); }
  .brand-name {
    font-family: "Open Sans", sans-serif; font-weight: 600;
    font-size: 17px; letter-spacing: 1px; color: var(--green);
  }
  .contact {
    position: absolute; right: 48px; top: 46px;
    text-align: right; font-family: "Open Sans", sans-serif; font-style: normal;
    font-size: 10.5px; line-height: 14px; color: #333;
  }
  .contact .company { color: var(--green); }
  .contact-row { display: flex; justify-content: flex-end; align-items: center; gap: 5px; }
  .contact-icon { width: 11px; height: 11px; }
  .footer-wave { position: absolute; left: 0; bottom: 0; width: 707px; height: 560px; z-index: 0; }
  .letter-body {
    position: absolute; left: 52px; top: 318px; width: 560px; z-index: 1;
    font-size: 11.2px; line-height: 14px;
  }
  .salutation { font-weight: 700; font-size: 15px; color: var(--heading); margin-bottom: 14px; }
  .letter-body p { margin-bottom: 14px; }
  .signature {
    position: absolute; left: 56px; top: 610px; width: 140px; height: 60px; z-index: 1;
    background: linear-gradient(90deg, #f1f1f1, #e7e7e7);
    border-radius: 4px;
  }
  .website {
    position: absolute; left: 40px; bottom: 24px; z-index: 2;
    font-family: "Open Sans", sans-serif; font-size: 15px;
    letter-spacing: .5px; color: #fff;
  }
</style>
</head>
<body>
<main class="letterhead">
  <header>
    <div class="brand">
      <span class="brand-dot"></span>
      <span class="brand-name">BRIGHT HARBOR DENTAL</span>
    </div>
    <address class="contact">
      <div class="company">Bright Harbor Dental</div>
      <div>4120 Lakeview Blvd,</div>
      <div>Suite 210 Arvada, CO 80002</div>
      <div class="contact-row">303-555-0142
        <svg class="contact-icon" viewBox="0 0 12 12"><circle cx="6" cy="6" r="6" fill="var(--green)"/><path d="M4 3.2l1 1.4-.6.8c.4.9 1.1 1.6 2 2l.8-.6 1.4 1-.5 1c-2.4-.3-4.3-2.2-4.6-4.6z" fill="#fff"/></svg>
      </div>
      <div class="contact-row">hello@brightharbordental.com
        <svg class="contact-icon" viewBox="0 0 12 12"><circle cx="6" cy="6" r="6" fill="var(--green)"/><rect x="3" y="4" width="6" height="4.2" fill="none" stroke="#fff" stroke-width=".9"/><path d="M3 4l3 2.3L9 4" fill="none" stroke="#fff" stroke-width=".9"/></svg>
      </div>
    </address>
  </header>

  <svg class="footer-wave" viewBox="0 0 707 560" preserveAspectRatio="none">
    <defs>
      <radialGradient id="soft-glow" cx="50%" cy="50%" r="50%">
        <stop offset="0" stop-color="var(--green-pale)"/>
        <stop offset="1" stop-color="var(--green-pale)" stop-opacity="0"/>
      </radialGradient>
    </defs>
    <ellipse role="img" aria-label="Faint decorative emblem" cx="580" cy="200" rx="130" ry="140" fill="url(#soft-glow)"/>
    <path d="M0 430 C 260 410 500 320 707 160 L707 560 L0 560 Z" fill="var(--green-pale)"/>
    <path d="M0 445 C 260 428 500 345 707 205 L707 560 L0 560 Z" fill="var(--green-light)"/>
    <path d="M0 458 C 260 442 500 365 707 235 L707 560 L0 560 Z" fill="#ffffff"/>
    <path d="M0 466 C 260 450 505 375 707 245 L707 560 L0 560 Z" fill="var(--green)"/>
  </svg>

  <section class="letter-body">
    <div class="salutation">Dear Mr. Avery,</div>
    <p>Lorem Ipsum is simply dummy text of the printing and typesetting industry. Lorem Ipsum has been the industry's standard dummy text ever since the 1500s, when an unknown printer took a galley of type and scrambled it to make a type specimen book. It has survived not only five centuries, but also the leap into electronic typesetting, remaining essentially unchanged.</p>
    <p>The standard chunk of Lorem Ipsum used since the 1500s is reproduced below for those interested. Sections 1.10.32 and 1.10.33 from "de Finibus Bonorum et Malorum" by Corvin are also reproduced in their exact original form, accompanied by English versions from the 1914 translation by H. Rowland</p>
    <p>Lorem Ipsum is simply dummy text of the printing and typesetting industry. Lorem Ipsum has been the industry's standard dummy text ever since the 1500s, when an unknown printer took a galley of type and scrambled it to make a type specimen book. It has survived not only five centuries, but also the leap into electronic typesetting, remaining essentially unchanged. It was popularised in the</p>
  </section>

  <div class="signature" role="img" aria-label="Handwritten signature"></div>

  <div class="website">www.brightharbordental.com</div>
</main>
</body>
</html>
```